Law firm business card

Information:

Me Mireille Dufontaine

website: dufontaine-legal.ca
email: mireille@dufontaine-legal.ca
Phone: 514 382-5167
Fax: 514 382-5169

Address:
Dufontaine and associates
2719 Belcourtier
Montreal, QC
H2K 3M9

Areas of Expertise:
Franchise Agreements, Financing, Acquisition, Real Estate Development, Commercial Agreements and Corporate Law

Target Market(s)

executives, companie managers

Industry/Entity Type

Business

Colors
f78f20
000000

Requirements
Must have
• Must use the logo, the logo is available here:

https://www.filecrate-example.com/sh/qyt3kwud82mfa0x/BBQTn7Lhvpe_kRTXwJM_GhcYb

```html
<!DOCTYPE html>
<html lang="en">
<head>
<meta charset="utf-8">
<title>Dufontaine and Associates – Business Card</title>
<link rel="stylesheet" href="https://fonts.googleapis.com/css2?family=Cinzel:wght@400;600&display=swap">
<style>
  :root {
    --orange: #f78f20;
    --white: #ffffff;
    --paper: #f7f7f7;
    --grey: #5f5f5f;
    --ink: #000000;
    --backdrop: #e4e4e2;
  }
  * { box-sizing: border-box; margin: 0; padding: 0; }
  html, body {
    width: 1200px; height: 900px; overflow: hidden;
    background: var(--backdrop);
  }
  .canvas { position: relative; width: 1200px; height: 900px; }
  .card {
    position: absolute; left: 250px; width: 700px; height: 400px;
    border-radius: 30px; overflow: hidden;
    box-shadow: 0 6px 18px rgba(0,0,0,0.18);
    font-family: "Cinzel", "Times New Roman", serif;
  }
  .card--front { top: 40px; }
  .card--back { top: 460px; }
  .card__art { position: absolute; inset: 0; width: 100%; height: 100%; }

  .firm-name {
    position: absolute; white-space: nowrap;
    color: var(--orange); font-weight: 600; font-size: 22px;
    letter-spacing: 0.5px; line-height: 1;
  }
  .card--front .firm-name { left: 52px; top: 168px; }
  .card--back .firm-name { left: 338px; top: 189px; transform: translateX(-50%); }

  .holder {
    position: absolute; left: 428px; top: 112px; color: var(--white);
    white-space: nowrap;
  }
  .holder__name { font-size: 21px; font-weight: 400; letter-spacing: 0.3px; }
  .holder__role { font-size: 17px; font-weight: 400; margin-top: 4px; letter-spacing: 0.3px; }

  .contacts {
    position: absolute; left: 420px; top: 258px; list-style: none;
    color: var(--white); font-size: 13.5px; line-height: 1.3;
  }
  .contacts__item { display: flex; align-items: flex-start; gap: 8px; margin-bottom: 3px; white-space: nowrap; }
  .contacts__icon { width: 14px; height: 14px; flex: none; margin-top: 1px; }
</style>
</head>
<body>
<main class="canvas">

  <section class="card card--front" aria-label="Business card front">
    <svg class="card__art" viewBox="0 0 700 400" aria-hidden="true">
      <defs>
        <linearGradient id="paperShade" x1="0" y1="0" x2="1" y2="1">
          <stop offset="0" stop-color="#ececec"/>
          <stop offset="0.45" stop-color="#ffffff"/>
          <stop offset="1" stop-color="#f6f6f6"/>
        </linearGradient>
      </defs>
      <rect class="card__base" width="700" height="400" fill="var(--orange)"/>
      <path class="card__corner-band" d="M640 0 H668 C688 40 698 100 700 150 V195 C692 122 672 55 640 0 Z" fill="var(--grey)"/>
      <path class="card__band" d="M0 0 H352 C500 95 488 310 300 400 H0 Z" fill="var(--grey)"/>
      <path class="card__panel" d="M0 0 H330 C478 90 465 305 280 400 H0 Z" fill="url(#paperShade)"/>
    </svg>

    <p class="firm-name">Dufontaine &amp; Associates</p>

    <div class="holder">
      <h1 class="holder__name">Mireille Dufontaine</h1>
      <p class="holder__role">Avocate / Lawyer</p>
    </div>

    <ul class="contacts">
      <li class="contacts__item">
        <svg class="contacts__icon" viewBox="0 0 14 14"><circle cx="7" cy="7" r="7" fill="#fff"/><path d="M7 3.2a2.4 2.4 0 0 0-2.4 2.4C4.6 7.4 7 10.8 7 10.8s2.4-3.4 2.4-5.2A2.4 2.4 0 0 0 7 3.2z" fill="var(--orange)"/><circle cx="7" cy="5.6" r="0.9" fill="#fff"/></svg>
        <span>2719 Belcourtier, Montreal,<br>QC H2K 3M9</span>
      </li>
      <li class="contacts__item">
        <svg class="contacts__icon" viewBox="0 0 14 14"><circle cx="7" cy="7" r="7" fill="#fff"/><path d="M4.4 3.4l1.4-.3.9 2-1 .8a5.5 5.5 0 0 0 2.4 2.4l.8-1 2 .9-.3 1.4c-3.4.3-6.5-2.8-6.2-6.2z" fill="var(--orange)"/></svg>
        <span>514 382-5167</span>
      </li>
      <li class="contacts__item">
        <svg class="contacts__icon" viewBox="0 0 14 14"><circle cx="7" cy="7" r="7" fill="#fff"/><rect x="4.5" y="3.3" width="5" height="2.4" fill="var(--orange)"/><rect x="3.3" y="6.1" width="7.4" height="3.2" rx="0.6" fill="var(--orange)"/><rect x="4.5" y="9" width="5" height="1.8" fill="var(--orange)"/></svg>
        <span>514 382-5169</span>
      </li>
      <li class="contacts__item">
        <svg class="contacts__icon" viewBox="0 0 14 14"><circle cx="7" cy="7" r="7" fill="#fff"/><rect x="3.3" y="4.4" width="7.4" height="5.2" rx="0.6" fill="var(--orange)"/><path d="M3.6 4.8L7 7.4l3.4-2.6" stroke="#fff" stroke-width="0.8" fill="none"/></svg>
        <span>mireille@dufontaine-legal.ca</span>
      </li>
      <li class="contacts__item">
        <svg class="contacts__icon" viewBox="0 0 14 14"><circle cx="7" cy="7" r="7" fill="#fff"/><circle cx="7" cy="7" r="3.8" fill="none" stroke="var(--orange)" stroke-width="0.9"/><ellipse cx="7" cy="7" rx="1.6" ry="3.8" fill="none" stroke="var(--orange)" stroke-width="0.8"/><path d="M3.2 7h7.6" stroke="var(--orange)" stroke-width="0.8"/></svg>
        <span>dufontaine-legal.ca</span>
      </li>
    </ul>
  </section>

  <section class="card card--back" aria-label="Business card back">
    <svg class="card__art" viewBox="0 0 700 400" aria-hidden="true">
      <rect class="card__base" width="700" height="400" fill="var(--orange)"/>
      <circle class="card__ring" cx="352" cy="206" r="262" fill="var(--grey)"/>
      <circle class="card__disc" cx="338" cy="200" r="250" fill="var(--paper)"/>
    </svg>

    <p class="firm-name">Dufontaine &amp; Associates</p>
  </section>

</main>
</body>
</html>
```